Business Card Design (NEW FILES)

ATTENTION: New vector files are available. Please update your design to reflect/use the new (better resolution) logo images.

Seeking a unique and professional business card design for a commercial drone photography/videography business. The layout should feature
the logo (attached) and include the following information:
Owen Tarrick
614-502-7738
www.skylarkreelworks.example
NRD Certified Remote Pilot

Owen Tarrick

```html
<!DOCTYPE html>
<html lang="en">
<head>
<meta charset="utf-8">
<title>Skylark Reelworks — Business Card</title>
<link rel="stylesheet" href="https://fonts.googleapis.com/css2?family=Open+Sans:wght@400;600;700;800&display=swap">
<style>
  :root {
    --stage: #232323;
    --navy: #1b1b4b;
    --orange: #ee8c52;
    --teal: #17b7b8;
    --white: #ffffff;
    --card-w: 620px;
    --card-h: 354px;
  }
  * { box-sizing: border-box; margin: 0; padding: 0; }
  html, body {
    width: 1200px; height: 780px; overflow: hidden;
    background: var(--stage);
    font-family: "Open Sans", Arial, sans-serif;
  }
  .sheet {
    width: 1200px; height: 780px;
    display: flex; flex-direction: column;
    align-items: center; justify-content: center; gap: 28px;
  }
  .card {
    position: relative;
    width: var(--card-w); height: var(--card-h);
    background: var(--navy);
    border-radius: 18px;
    overflow: hidden;
  }
  .card__bands {
    position: absolute; left: 0; top: 0;
    width: 100%; height: 100%;
  }
  .brand {
    position: absolute;
    display: flex; align-items: center; gap: 12px;
    color: var(--white);
    font-weight: 600;
    letter-spacing: 0.04em;
    text-transform: uppercase;
    white-space: nowrap;
  }
  .brand__dot {
    flex: none;
    border-radius: 50%;
    background: var(--orange);
  }
  .card--front .brand { left: 50%; top: 150px; transform: translateX(-50%); font-size: 34px; }
  .card--front .brand__dot { width: 34px; height: 34px; }
  .card--back .brand { left: 40px; top: 160px; font-size: 20px; gap: 9px; }
  .card--back .brand__dot { width: 20px; height: 20px; }
  .divider {
    position: absolute; left: 318px; top: 86px;
    width: 1px; height: 176px;
    background: var(--orange);
  }
  .contact {
    position: absolute; left: 352px; top: 108px;
    color: var(--white);
    white-space: nowrap;
  }
  .contact__name {
    font-size: 30px; font-weight: 800; line-height: 1.05;
  }
  .contact__first { color: var(--orange); }
  .contact__role {
    font-size: 14px; font-weight: 600; margin-top: 2px;
  }
  .contact__list {
    list-style: none; margin-top: 22px;
    font-size: 13px; font-weight: 400;
  }
  .contact__item {
    display: flex; align-items: center; gap: 8px; margin-bottom: 6px;
  }
  .contact__icon { width: 13px; height: 13px; flex: none; }
</style>
</head>
<body>
<main class="sheet">

  <section class="card card--front" aria-label="Card front">
    <svg class="card__bands" viewBox="0 0 620 354" aria-hidden="true">
      <path d="M0 340 H352 L368 354 H0 Z" fill="var(--orange)"/>
      <path d="M346 324 H620 V354 H378 Z" fill="var(--teal)"/>
    </svg>
    <div class="brand"><span class="brand__dot"></span>Skylark Reelworks</div>
  </section>

  <section class="card card--back" aria-label="Card back">
    <svg class="card__bands" viewBox="0 0 620 354" aria-hidden="true">
      <path d="M0 340 H352 L368 354 H0 Z" fill="var(--orange)"/>
      <path d="M346 324 H620 V354 H378 Z" fill="var(--teal)"/>
    </svg>
    <div class="brand"><span class="brand__dot"></span>Skylark Reelworks</div>
    <div class="divider"></div>
    <div class="contact">
      <h1 class="contact__name"><span class="contact__first">Owen</span> Tarrick</h1>
      <p class="contact__role">NRD Certified Remote Pilot</p>
      <ul class="contact__list">
        <li class="contact__item">
          <svg class="contact__icon" viewBox="0 0 24 24" aria-hidden="true">
            <path fill="var(--orange)" d="M6.6 10.8a15.1 15.1 0 0 0 6.6 6.6l2.2-2.2a1 1 0 0 1 1-.25 11.4 11.4 0 0 0 3.6.57 1 1 0 0 1 1 1V20a1 1 0 0 1-1 1A17 17 0 0 1 3 4a1 1 0 0 1 1-1h3.5a1 1 0 0 1 1 1c0 1.250.2 2.450.57 3.570a1 1 0 0 1-.25 1z"/>
          </svg>
          614-502-7738
        </li>
        <li class="contact__item">
          <svg class="contact__icon" viewBox="0 0 24 24" aria-hidden="true">
            <circle cx="12" cy="12" r="10" fill="none" stroke="var(--orange)" stroke-width="2.4"/>
            <path d="M2 12h20M12 2c3 3 3 17 0 20M12 2c-3 3-3 17 0 20" fill="none" stroke="var(--orange)" stroke-width="2"/>
          </svg>
          www.skylarkreelworks.example
        </li>
      </ul>
    </div>
  </section>

</main>
</body>
</html>
```